High Tech Real Estate Startup needs a business card

We are developing an innovative real estate marketing product based around advanced search and virtual reality.

We talk to people, we need business cards.

Target Market(s)

The target market is technology professionals and realtors.

Contact Information for Business Card

The information to be included will include

Name
Title
Phone Number
E-mail Address
www.zelquin.com

It should use simple iconography for each one of those fields.

Font styles to use
Other font styles liked:
• Co, Jubilat, Avenir

Colors

Designer to choose colors to be used in the design.

Requirements
Must have
• Clean aesthetic,
• Good use of negative space.
• It should use our company logo, shown in the attached file. It is able to use the negative of that logo (coloured font and white background) and I have attached other acceptable accent colours in a swatch file.
Should not have
• Should not be too busy
• No extraneous text (slogans, tag lines etc)

```html
<!DOCTYPE html>
<html lang="en">
<head>
<meta charset="utf-8">
<title>Zelquin Business Card</title>
<link rel="stylesheet" href="https://fonts.googleapis.com/css2?family=Montserrat:wght@500&family=Roboto+Condensed:wght@400;700&display=swap">
<style>
  :root {
    --page: #ecebe8;
    --teal: #13b8bd;
    --teal-light: #22c4c7;
    --white: #ffffff;
    --shadow: rgba(0, 0, 0, 0.18);
  }
  * { margin: 0; padding: 0; box-sizing: border-box; }
  html, body { width: 1200px; height: 911px; overflow: hidden; }
  body {
    background: var(--page);
    display: flex;
    align-items: center;
    justify-content: center;
    gap: 40px;
  }
  .card {
    position: relative;
    width: 540px;
    height: 309px;
    background: linear-gradient(135deg, var(--teal-light) 0%, var(--teal) 55%);
    box-shadow: 0 10px 24px var(--shadow);
    color: var(--white);
    overflow: hidden;
  }
  .wordmark {
    font-family: "Montserrat", sans-serif;
    font-weight: 500;
    letter-spacing: 0.02em;
    line-height: 1;
  }
  .card-front .wordmark {
    position: absolute;
    top: 30px;
    left: 262px;
    font-size: 54px;
  }
  .identity {
    position: absolute;
    left: 0;
    bottom: 28px;
    display: flex;
    align-items: flex-end;
  }
  .identity-tab {
    width: 28px;
    height: 16px;
    background: var(--white);
    margin-right: 18px;
    margin-bottom: 70px;
  }
  .person {
    font-family: "Roboto Condensed", sans-serif;
  }
  .person-name {
    font-weight: 700;
    font-size: 19px;
    letter-spacing: 0.01em;
    line-height: 1.05;
  }
  .person-title {
    font-weight: 400;
    font-size: 14px;
    margin-bottom: 16px;
  }
  .contact-list { list-style: none; }
  .contact-list li {
    display: flex;
    align-items: center;
    gap: 8px;
    font-size: 13px;
    line-height: 1.45;
  }
  .contact-list svg { width: 11px; height: 11px; flex: none; }
  .card-back {
    display: flex;
    flex-direction: column;
    align-items: center;
    justify-content: center;
    gap: 18px;
  }
  .card-back .wordmark { font-size: 64px; }
  .web-line {
    font-family: "Montserrat", sans-serif;
    font-weight: 500;
    font-size: 11px;
    letter-spacing: 0.42em;
    text-transform: uppercase;
  }
</style>
</head>
<body>
  <section class="card card-front" aria-label="Business card front">
    <div class="wordmark">ZELQUIN</div>
    <div class="identity">
      <div class="identity-tab"></div>
      <div class="person">
        <p class="person-name">DANA REYES</p>
        <p class="person-title">CEO/FOUNDER</p>
        <ul class="contact-list">
          <li>
            <svg viewBox="0 0 12 12" aria-hidden="true"><path fill="#fff" d="M2.5 1h2l1 3-1.3.9a6.5 6.5 0 0 0 2.9 2.9L8 6.5l3 1v2A1.5 1.5 0 0 1 9.5 11 8.5 8.5 0 0 1 1 2.5 1.5 1.5 0 0 1 2.5 1z"/></svg>
            555 014 2290
          </li>
          <li>
            <svg viewBox="0 0 12 12" aria-hidden="true"><rect x="0.5" y="2" width="11" height="8" fill="#fff"/><path d="M1 2.5 6 6.5 11 2.5" fill="none" stroke="#13b8bd" stroke-width="1.2"/></svg>
            dana@zelquin.com
          </li>
          <li>
            <svg viewBox="0 0 12 12" aria-hidden="true"><circle cx="6" cy="6" r="5.5" fill="#fff"/><path d="M0.8 6h10.4M6 0.6c-2.4 2.8-2.4 8 0 10.8M6 0.6c2.4 2.8 2.4 8 0 10.8" fill="none" stroke="#13b8bd" stroke-width="0.9"/></svg>
            www.zelquin.com
          </li>
        </ul>
      </div>
    </div>
  </section>

  <section class="card card-back" aria-label="Business card back">
    <p class="web-line">www.zelquin.com</p>
    <div class="wordmark">ZELQUIN</div>
  </section>
</body>
</html>
```